Web Developer Needs a Business Card Design

I need a personal business card design that represents me as a web developer for potential employers. I would like the background to be a dark color on the front for contrast with my logo and name. The back will have all my information along with a smaller version of the logo. I want something with a modern look and feel, not too conservative. This will be used for potential employers and freelance work.

Industry/Entity Type

Business

Contact Information for Business Card

Front should have my logo and name. The back should have all my personal information which would include: name: Tom Varulek, phone: 570-614-3098, email: tomvarulek@quillbox.net, website url: www.tomvarulek.net, logo, web developer.

Font styles to use
Sans Serif

Requirements
Must have
• Must include my logo. The color palette base color will be the logo color.

```html
<!DOCTYPE html>
<html lang="en">
<head>
<meta charset="utf-8">
<title>Tom Varulek – Business Card</title>
<link rel="stylesheet" href="https://fonts.googleapis.com/css2?family=Open+Sans:wght@300;400;600;700&family=Crimson+Text:wght@400&display=swap">
<style>
  :root {
    --stage: #141414;
    --card-black: #0c0c0c;
    --card-edge: #2a2a2a;
    --silver: #d6d6d6;
    --silver-dim: #9a9a9a;
    --teal: #79cbb8;
    --ink: #111111;
    --rule: #2e2e2e;
  }
  * { box-sizing: border-box; margin: 0; padding: 0; }
  html, body { width: 1200px; height: 924px; overflow: hidden; background: var(--stage); }
  .stage { position: relative; width: 1200px; height: 924px; }

  .card {
    position: absolute;
    width: 620px; height: 354px;
    border-radius: 18px;
    background: var(--card-black);
    box-shadow: 0 0 0 1px var(--card-edge), 0 18px 40px rgba(0,0,0,.55);
    overflow: hidden;
  }
  .card--front { left: 150px; top: 64px; }
  .card--back  { left: 430px; top: 500px; }

  /* front */
  .front-mark {
    position: absolute; left: 50%; top: 44px;
    width: 176px; height: 176px; margin-left: -88px;
    border-radius: 50%;
    border: 9px solid var(--silver);
    display: flex; align-items: center; justify-content: center;
  }
  .mark-name {
    font-family: "Open Sans", sans-serif;
    font-weight: 600; font-size: 22px; letter-spacing: .5px;
  }
  .front-mark .mark-name { color: var(--silver); }
  .front-name {
    position: absolute; left: 0; right: 0; top: 246px;
    text-align: center;
    font-family: "Open Sans", sans-serif;
    font-size: 40px; color: var(--silver);
  }
  .front-name .first { font-weight: 300; color: var(--silver-dim); }
  .front-name .last { font-weight: 600; }

  /* back */
  .back-band {
    position: absolute; left: 0; right: 0; top: 196px; bottom: 0;
    background: var(--teal);
  }
  .back-rule {
    position: absolute; top: 160px; height: 2px; background: var(--rule);
  }
  .back-rule--left { left: 0; width: 210px; }
  .back-rule--right { right: 0; width: 210px; }
  .back-mark {
    position: absolute; left: 50%; top: 40px;
    width: 136px; height: 136px; margin-left: -68px;
    border-radius: 50%;
    border: 7px solid var(--teal);
    display: flex; align-items: center; justify-content: center;
  }
  .back-mark .mark-name { color: var(--teal); font-size: 17px; }

  .identity {
    position: absolute; left: 60px; top: 236px; width: 250px;
    text-align: right;
  }
  .identity-name {
    font-family: "Crimson Text", serif;
    font-size: 36px; line-height: 1; color: var(--ink);
  }
  .identity-role {
    font-family: "Open Sans", sans-serif;
    font-size: 19px; color: var(--ink); margin-top: 4px;
  }
  .divider {
    position: absolute; left: 330px; top: 218px; width: 2px; height: 108px;
    background: var(--ink);
  }
  .contact {
    position: absolute; left: 350px; top: 228px;
    list-style: none;
    font-family: "Open Sans", sans-serif; font-size: 16px; color: var(--ink);
  }
  .contact li { display: flex; align-items: center; gap: 7px; height: 27px; }
  .contact svg { width: 15px; height: 15px; flex: none; }
</style>
</head>
<body>
<main class="stage">

  <section class="card card--front" aria-label="Card front">
    <div class="front-mark"><span class="mark-name">Tom Varulek</span></div>
    <p class="front-name"><span class="first">Tom</span> <span class="last">Varulek</span></p>
  </section>

  <section class="card card--back" aria-label="Card back">
    <div class="back-band"></div>
    <div class="back-rule back-rule--left"></div>
    <div class="back-rule back-rule--right"></div>
    <div class="back-mark"><span class="mark-name">Tom Varulek</span></div>

    <div class="identity">
      <p class="identity-name">Tom Varulek</p>
      <p class="identity-role">web developer</p>
    </div>
    <div class="divider"></div>

    <ul class="contact">
      <li>
        <svg viewBox="0 0 16 16" aria-hidden="true"><rect width="16" height="16" rx="2" fill="#111"/><path d="M5 3.5l1.6 2.2-1 1c.6 1.4 1.7 2.5 3.1 3.1l1-1 2.2 1.6-1 1.6c-3.6-.4-6.1-2.9-6.5-6.5z" fill="#79cbb8"/></svg>
        570-614-3098
      </li>
      <li>
        <svg viewBox="0 0 16 16" aria-hidden="true"><rect width="16" height="16" rx="2" fill="#111"/><rect x="3" y="4.5" width="10" height="7" fill="none" stroke="#79cbb8" stroke-width="1.2"/><path d="M3 4.5l5 4 5-4" fill="none" stroke="#79cbb8" stroke-width="1.2"/></svg>
        tomvarulek@quillbox.net
      </li>
      <li>
        <svg viewBox="0 0 16 16" aria-hidden="true"><rect width="16" height="16" rx="2" fill="#111"/><circle cx="8" cy="8" r="4.5" fill="none" stroke="#79cbb8" stroke-width="1.2"/><path d="M3.5 8h9M8 3.5c-2 2.5-2 6.5 0 9M8 3.5c2 2.5 2 6.5 0 9" fill="none" stroke="#79cbb8" stroke-width="1"/></svg>
        www.tomvarulek.net
      </li>
    </ul>
  </section>

</main>
</body>
</html>
```